Tech business card design

We need an amazing business card design for our new business 'Pexla' a marketing tech startup based in Sydney, Australia. We provide an online marketplace for businesses to search and buy advertising media, connect with service providers and learn more about marketing. We wish to communicate 'cool tech', reliability and professionalism and design based around our logo.

Target Market(s)

Business Owners

Contact Information for Business Card

Name
Position
Email Address
Website
Phone Number

Font styles to use
Other font styles liked:
• Avenir & Avenir Next

Colors

Designer to choose colors to be used in the design.

```html
<!DOCTYPE html>
<html lang="en">
<head>
<meta charset="utf-8">
<title>Pexla business card</title>
<link rel="stylesheet" href="https://fonts.googleapis.com/css2?family=Work+Sans:wght@400;500;800&display=swap">
<style>
  :root {
    --backdrop: #1c1c1d;
    --card-navy: #13144a;
    --card-navy-light: #1d1f5c;
    --ink: #ffffff;
    --ink-soft: #e4e6f2;
  }
  * { margin: 0; padding: 0; box-sizing: border-box; }
  html, body { width: 1200px; height: 900px; overflow: hidden; }
  body {
    background: var(--backdrop);
    font-family: "Work Sans", Arial, sans-serif;
    display: flex;
    flex-direction: column;
    align-items: center;
    justify-content: center;
    gap: 44px;
  }
  .card {
    position: relative;
    width: 640px;
    height: 366px;
    background: linear-gradient(135deg, var(--card-navy) 0%, var(--card-navy) 55%, var(--card-navy-light) 100%);
    color: var(--ink);
  }
  .wordmark {
    font-weight: 800;
    color: var(--ink);
    letter-spacing: -1px;
    line-height: 1;
  }
  .card-front .wordmark {
    position: absolute;
    left: 50%;
    top: 50%;
    transform: translate(-46%, -58%);
    font-size: 104px;
  }
  .card-back .wordmark {
    position: absolute;
    left: 52px;
    top: 132px;
    font-size: 108px;
  }
  .divider {
    position: absolute;
    left: 372px;
    top: 96px;
    width: 1.5px;
    height: 190px;
    background: var(--ink-soft);
  }
  .contact {
    position: absolute;
    left: 398px;
    top: 100px;
    color: var(--ink-soft);
  }
  .contact-name { font-size: 24px; font-weight: 500; color: var(--ink); }
  .contact-role { font-size: 14px; margin-top: 2px; }
  .contact-address { font-size: 15px; line-height: 21px; margin-top: 16px; letter-spacing: 0.3px; }
  .contact-lines { list-style: none; margin-top: 12px; font-size: 15px; line-height: 23px; letter-spacing: 0.3px; }
  .contact-lines li { display: flex; align-items: center; gap: 10px; }
  .contact-lines svg { width: 12px; height: 12px; flex: none; }
</style>
</head>
<body>
  <section class="card card-front" aria-label="Card front">
    <div class="wordmark">pexla</div>
  </section>

  <section class="card card-back" aria-label="Card back">
    <div class="wordmark">pexla</div>
    <div class="divider"></div>
    <div class="contact">
      <p class="contact-name">Daniel Moreau</p>
      <p class="contact-role">Director</p>
      <p class="contact-address">2815 Linden Avenue<br>Sydney, NSW 2000</p>
      <ul class="contact-lines">
        <li>
          <svg viewBox="0 0 12 12" aria-hidden="true"><path d="M2.5 1h2l1 2.6-1.3.9a6 6 0 0 0 3.3 3.3l.9-1.3 2.6 1v2a1 1 0 0 1-1 1A9 9 0 0 1 1.5 2a1 1 0 0 1 1-1z" fill="none" stroke="currentColor" stroke-width="1.1"/></svg>
          +612 5830-7194
        </li>
        <li>
          <svg viewBox="0 0 12 12" aria-hidden="true"><rect x="1" y="2.5" width="10" height="7" fill="none" stroke="currentColor" stroke-width="1.1"/><path d="M1 2.5l5 4 5-4" fill="none" stroke="currentColor" stroke-width="1.1"/></svg>
          info@pexla.com
        </li>
        <li>
          <svg viewBox="0 0 12 12" aria-hidden="true"><circle cx="6" cy="6" r="5" fill="none" stroke="currentColor" stroke-width="1"/><ellipse cx="6" cy="6" rx="2.2" ry="5" fill="none" stroke="currentColor" stroke-width="1"/><path d="M1 6h10M2 3.5h8M2 8.5h8" stroke="currentColor" stroke-width="0.8"/></svg>
          www.pexla.com
        </li>
      </ul>
    </div>
  </section>
</body>
</html>
```